Blue Harbor Supply is looking for a new bag design for Blue Harbor Frost Away

Need a new updated design for our signature product, Blue Harbor Frost Away. Our environmentally friendly granular ice melt product is a leader in the alternative road salt industry. We would like to emphasize the highest quality and a safer product for pet owners. This would be put on retail store shelves. More product updates would be available to the winning designer also. Back of the bag can remain as it is currently, just looking for a shelf ready, eye-popping front of our bag. Current bag front and back uploaded.
Updates
Please incorporate this picture of a puppy on the front of the bag: Google drive: https://files.quillbox.example/d/7xRtPq2mLvNa9KcWe4HsJbYuZ0fGd3Tq/open

```html
<!DOCTYPE html>
<html lang="en">
<head>
<meta charset="utf-8">
<title>Blue Harbor Frost Away – 50 lb bag</title>
<link rel="stylesheet" href="https://fonts.googleapis.com/css2?family=Bebas+Neue&family=Montserrat:wght@400;600;700&display=swap">
<style>
  :root {
    --bg: #f3f3f5;
    --green-top: #2c9f2c;
    --green-mid: #0f7f1f;
    --green-low: #1e9523;
    --lime: #9bcf3e;
    --lime-soft: #8fcf4a;
    --white: #ffffff;
    --badge-text: #2f6d12;
    --photo-a: #e9ecef;
    --photo-b: #9aa3aa;
  }
  * { margin: 0; padding: 0; box-sizing: border-box; }
  html, body { width: 950px; height: 1200px; overflow: hidden; background: var(--bg); }
  .canvas { position: relative; width: 950px; height: 1200px; }

  .bag-face {
    position: absolute; left: 266px; top: 20px; width: 418px; height: 1160px;
    background: linear-gradient(180deg, var(--green-top) 0%, var(--green-top) 8.4%, #26962a 8.5%, #18882a 35%, var(--green-mid) 50%, #148a22 70%, var(--green-low) 100%);
    color: var(--white); font-family: "Montserrat", sans-serif; overflow: hidden;
  }
  .abs { position: absolute; }

  .brand-title { top: 138px; left: 0; width: 100%; text-align: center;
    font-family: "Bebas Neue", sans-serif; font-size: 60px; line-height: 1; letter-spacing: 0; }
  .brand-sub { top: 198px; left: 0; width: 100%; text-align: center;
    font-weight: 600; font-size: 20px; letter-spacing: 6px; }
  .tm { font-size: 10px; letter-spacing: 0; vertical-align: top; }

  .claim-eco { top: 253px; left: 0; width: 100%; text-align: center; color: var(--lime);
    font-family: "Bebas Neue", sans-serif; font-size: 30px; line-height: 1; }
  .claim-formula { top: 284px; left: 0; width: 100%; text-align: center;
    font-weight: 600; font-size: 13.5px; letter-spacing: 1.6px; }

  .benefits { top: 344px; left: 44px; list-style: none; }
  .benefits li { display: flex; align-items: center; gap: 6px; height: 29px;
    font-family: "Bebas Neue", sans-serif; font-size: 19px; line-height: 1; }
  .benefits svg { width: 18px; height: 18px; flex: none; }

  .temp { top: 341px; left: 298px; text-align: left; font-family: "Bebas Neue", sans-serif; line-height: 1; }
  .temp-label { font-size: 21px; }
  .temp-value { font-size: 48px; margin-top: 2px; }

  .directions-note { top: 429px; left: 66px; color: var(--lime-soft); font-weight: 600; font-size: 11.5px; }

  .badge { top: 457px; left: 56px; width: 92px; height: 92px; border-radius: 50%;
    background: var(--lime); color: var(--badge-text); display: flex; align-items: center; justify-content: center;
    text-align: center; font-family: "Bebas Neue", sans-serif; font-size: 12.5px; line-height: 1.05; }

  .maker { top: 494px; left: 156px; width: 104px; display: flex; align-items: center; gap: 5px;
    font-weight: 700; font-size: 13px; line-height: 1.1; }
  .maker-dot { width: 10px; height: 10px; border-radius: 50%; background: var(--lime); flex: none; }

  .puppy-ring { top: 411px; left: 271px; width: 128px; height: 128px; border-radius: 50%; background: var(--lime); }
  .puppy-photo { position: absolute; left: 4px; top: 4px; width: 116px; height: 116px; border-radius: 50%;
    background: radial-gradient(circle at 45% 45%, var(--photo-b) 0%, #5d666c 45%, var(--photo-a) 75%); }

  .net-weight { top: 545px; left: 0; width: 100%; text-align: center; font-weight: 700; font-size: 23px; letter-spacing: 0.5px; }

  .back-panel { top: 590px; left: 37px; width: 343px; height: 470px; transform: rotate(180deg);
    display: flex; flex-direction: column; gap: 6px; font-size: 5.8px; line-height: 7.4px; }
  .back-title { text-align: center; }
  .back-title .name { font-family: "Bebas Neue", sans-serif; font-size: 32px; line-height: 1; }
  .back-title .sub { font-weight: 600; font-size: 11px; letter-spacing: 4px; line-height: 1.2; }
  .back-panel h3 { font-weight: 700; font-size: 10px; line-height: 13px; text-align: right; }
  .back-panel p { text-align: justify; }
  .ingredients { display: grid; grid-template-columns: 60px 1fr; }
  .company-row { display: flex; justify-content: space-between; align-items: flex-start; margin-top: 4px; }
  .address { font-weight: 700; line-height: 8px; }
  .back-maker { display: flex; align-items: center; gap: 4px; font-weight: 700; font-size: 10px; line-height: 1.1; }
  .back-maker .maker-dot { width: 8px; height: 8px; }
</style>
</head>
<body>
<div class="canvas">
  <section class="bag-face">
    <h1 class="abs brand-title">BLUE HARBOR</h1>
    <div class="abs brand-sub">frost away <span class="tm">TM</span></div>

    <div class="abs claim-eco">ENVIRONMENTALLY FRIENDLY</div>
    <div class="abs claim-formula">HIGH PERFORMANCE FORMULA</div>

    <ul class="abs benefits">
      <li><svg viewBox="0 0 20 20"><path d="M3 10.5l4.5 4.5L17 5" fill="none" stroke="var(--lime)" stroke-width="3" stroke-linecap="round" stroke-linejoin="round"/></svg>REMOVES TWICE AS MUCH ICE &amp; SNOW</li>
      <li><svg viewBox="0 0 20 20"><path d="M3 10.5l4.5 4.5L17 5" fill="none" stroke="var(--lime)" stroke-width="3" stroke-linecap="round" stroke-linejoin="round"/></svg>SAFER FOR CHILDREN &amp; PETS</li>
      <li><svg viewBox="0 0 20 20"><path d="M3 10.5l4.5 4.5L17 5" fill="none" stroke="var(--lime)" stroke-width="3" stroke-linecap="round" stroke-linejoin="round"/></svg>LESS CORROSIVE THAN OTHER SALTS</li>
    </ul>

    <div class="abs temp">
      <div class="temp-label">EFFECTIVE TO</div>
      <div class="temp-value">-25° F</div>
    </div>

    <div class="abs directions-note">See Back for directions</div>

    <div class="abs badge">THIS BAG TREATS<br>THE SAME AREA<br>AS 100 LBS<br>OF ANY OTHER<br>BRAND</div>

    <div class="abs maker"><span class="maker-dot"></span><span>Blue Harbor Supply</span></div>

    <div class="abs puppy-ring">
      <div class="puppy-photo" role="img" aria-label="Photo of a black puppy sitting in the snow"></div>
    </div>

    <div class="abs net-weight">NET WT 50 LB / 22.68 KG</div>

    <div class="abs back-panel">
      <div class="back-title">
        <div class="name">BLUE HARBOR</div>
        <div class="sub">frost away <span class="tm">TM</span></div>
      </div>
      <p>Blue Harbor Frost Away blends naturally occurring granular ice melter with a liquid deicer for a high performance product that is safer around concrete, asphalt, metal, animals, plants and waterways. It works at much colder temperatures (-25°F / -31°C), acts faster and lasts longer, so less product is needed. Use about half the rate of other ice melters. The green tint shows where product has been spread and fades in sunlight.</p>
      <h3>Directions for use:</h3>
      <p>For best results, clear existing snow and slush before applying. Spread evenly at about 5 lbs per 1,000 sq. ft. Melting begins at once. When snow and ice are soft enough, shovel off what remains. Thick buildup may need a second pass.</p>
      <h3>Precaution:</h3>
      <p>Frost Away will not harm properly mixed, poured and cured concrete. Do not use on concrete less than one year old. Natural freeze and thaw cycles can damage poor quality concrete, and overuse may cause surface flaking or scaling. Remove water and slush after melting to limit refreezing. Any deicer can harm plants and lawns when placed directly on or near them, so apply only the rate needed and keep product on paved surfaces.</p>
      <h3>Contains:</h3>
      <p>Enhanced solution with potassium acetate and other non-hazardous components and corrosion inhibitors.</p>
      <div class="ingredients"><span>NaCl</span><span>CAS NO. 7647-14-5</span><span>K Acetate</span><span>CAS NO. 127-08-2</span></div>
      <p><strong>Disclaimer:</strong> No warranty, express or implied, is made for this product or its fitness for any purpose. If product sets up or hardens, roll the bag on the ground to loosen it.</p>
      <div class="company-row">
        <div class="address">Blue Harbor Supply Inc.<br>Harlow Bay, MN 55731<br>218-555-0147<br>1-800-555-0193<br>www.blueharborsupply.example</div>
        <div class="back-maker"><span class="maker-dot"></span><span>Blue Harbor Supply</span></div>
      </div>
    </div>
  </section>
</div>
</body>
</html>
```